Dental Practice Billboard Design

We are a newer dental practice in need of a simple but appealing billboard for our growing dental practice to attract new patients. The practice is owned by husband and wife dentists and is family friendly in a small town in Kentucky. We try to be very friendly and caring to our patients. Would prefer a blue background for the billboard and our tooth logo to be prominent. We are partial to the Patua One font used in the image below but please feel free to tweak it as you deem necessary. The shape of the uppercase D and lowercase g are why we like that font, so fonts with a similarly shaped “D” and “g” would work as well. Please include our phone number (555) 847-1390. Please see our website Harlowbrookdentistry.example for more info on the practice if needed. Thank you! Looking forward to seeing your creation.
Updates

The dimensions will be 12ft x 24ft (3.6576m x 7.3152m). Apologies for not including this in the original prompt. Thank you all for your submissions.

Industry/Entity Type

Dental

Font styles to use
Other font styles liked:
• Patua One

Colors
0054AA
0677BA
7BADD7
CADEEF
E8F1F8
0094D4
00A9DD
6FCCEA
C7EBF8
E9F6FB
00AB8E
00BBA5
67D7C9
C6EFE9
E9F9F6
59FF00
82FF00
B8FF75
E3FFCB
F4FFEA

Requirements
Must have
• Phone number, website, Logo, Practice name “Harlow Brook Dentistry”
Should not have
• A tagline or slogan

```html
<!DOCTYPE html>
<html lang="en">
<head>
<meta charset="utf-8">
<title>Harlow Brook Dentistry Billboard</title>
<link rel="stylesheet" href="https://fonts.googleapis.com/css2?family=Patua+One&family=Poppins:wght@500;600;800&display=swap">
<style>
  :root {
    --page: #ececec;
    --white: #ffffff;
    --blue-deep: #0a2c86;
    --blue: #0b4fb4;
    --green-deep: #0c7f2a;
    --green: #18b418;
    --green-bright: #2fc41e;
    --photo-light: #efe6dc;
    --photo-mid: #c9b9a8;
    --photo-denim: #5a78a8;
  }
  * { margin: 0; padding: 0; box-sizing: border-box; }
  html, body { width: 968px; height: 1200px; overflow: hidden; background: var(--page); }
  .billboard {
    position: absolute; left: 24px; top: 466px;
    width: 920px; height: 268px;
    background: var(--white);
    box-shadow: 6px 10px 18px rgba(0,0,0,0.28);
    overflow: hidden;
  }
  .billboard-shapes { position: absolute; inset: 0; }
  .website {
    position: absolute; left: 320px; top: 24px;
    font-family: "Patua One", serif; font-size: 30.5px; line-height: 1;
    color: var(--white); white-space: nowrap;
  }
  .website .accent { color: var(--green-bright); }
  .services-label {
    position: absolute; left: 320px; top: 73px;
    height: 23px; padding: 0 10px;
    background: var(--green); border-radius: 12px;
    font-family: "Poppins", sans-serif; font-weight: 800; font-size: 16px;
    letter-spacing: 1px; line-height: 23px; color: var(--white);
  }
  .service-column {
    position: absolute; top: 106px; list-style: none;
    font-family: "Poppins", sans-serif; font-weight: 500; font-size: 14.5px;
    line-height: 22.5px; color: var(--white);
  }
  .service-column li { display: flex; align-items: center; gap: 6px; white-space: nowrap; }
  .tick { width: 9px; height: 9px; flex: none; }
  .col-1 { left: 322px; } .col-2 { left: 465px; } .col-3 { left: 627px; } .col-4 { left: 755px; }
  .phone {
    position: absolute; left: 318px; top: 208px;
    display: flex; align-items: center; gap: 8px;
    font-family: "Poppins", sans-serif; font-weight: 600; font-size: 35px;
    letter-spacing: -0.5px;
    line-height: 1; color: var(--white); white-space: nowrap;
  }
  .phone-icon { width: 38px; height: 38px; flex: none; }
  .brand {
    position: absolute; left: 712px; top: 203px;
    display: flex; align-items: center; gap: 10px;
  }
  .brand-dot { width: 16px; height: 16px; border-radius: 50%; background: var(--green); flex: none; }
  .brand-name {
    font-family: "Patua One", serif; font-size: 22px; line-height: 1.05;
    color: var(--blue);
  }
</style>
</head>
<body>
<section class="billboard">
  <svg class="billboard-shapes" viewBox="0 0 920 268" width="920" height="268">
    <defs>
      <linearGradient id="blueGrad" x1="0" x2="1" y1="0" y2="0">
        <stop offset="0" stop-color="#0a2c86"/>
        <stop offset="1" stop-color="#0b4fb4"/>
      </linearGradient>
      <linearGradient id="greenGrad" x1="0" x2="1" y1="0" y2="0">
        <stop offset="0" stop-color="#0c7f2a"/>
        <stop offset="1" stop-color="#18b418"/>
      </linearGradient>
      <linearGradient id="photoGrad" x1="0" x2="0" y1="0" y2="1">
        <stop offset="0" stop-color="#efe6dc"/>
        <stop offset="0.5" stop-color="#c9b9a8"/>
        <stop offset="1" stop-color="#5a78a8"/>
      </linearGradient>
    </defs>
    <rect class="services-panel" x="240" y="0" width="680" height="183" fill="url(#blueGrad)"/>
    <rect class="phone-band" x="240" y="187" width="455" height="81" fill="url(#greenGrad)"/>
    <path class="photo-area" d="M0 0 H265 C320 50 318 200 205 268 H0 Z" fill="#ffffff"/>
    <path class="photo-edge" d="M265 0 C320 50 318 200 205 268" fill="none" stroke="#18b418" stroke-width="8"/>
    <rect x="32" y="30" width="190" height="232" rx="20" fill="url(#photoGrad)" role="img" aria-label="Photo of a smiling family of three sitting together"/>
  </svg>

  <p class="website">Harlowbrookdentistry<span class="accent">.example</span></p>
  <div class="services-label">OUR SERVICES</div>

  <ul class="service-column col-1">
    <li><svg class="tick" viewBox="0 0 10 10"><circle cx="5" cy="5" r="5" fill="#2fc41e"/><path d="M2.8 5.2l1.5 1.5 2.9-3" stroke="#0a2c86" stroke-width="1.3" fill="none"/></svg>Crowns</li>
    <li><svg class="tick" viewBox="0 0 10 10"><circle cx="5" cy="5" r="5" fill="#2fc41e"/><path d="M2.8 5.2l1.5 1.5 2.9-3" stroke="#0a2c86" stroke-width="1.3" fill="none"/></svg>Root Canals</li>
    <li><svg class="tick" viewBox="0 0 10 10"><circle cx="5" cy="5" r="5" fill="#2fc41e"/><path d="M2.8 5.2l1.5 1.5 2.9-3" stroke="#0a2c86" stroke-width="1.3" fill="none"/></svg>Extractions</li>
  </ul>
  <ul class="service-column col-2">
    <li><svg class="tick" viewBox="0 0 10 10"><circle cx="5" cy="5" r="5" fill="#2fc41e"/><path d="M2.8 5.2l1.5 1.5 2.9-3" stroke="#0a2c86" stroke-width="1.3" fill="none"/></svg>Implants</li>
    <li><svg class="tick" viewBox="0 0 10 10"><circle cx="5" cy="5" r="5" fill="#2fc41e"/><path d="M2.8 5.2l1.5 1.5 2.9-3" stroke="#0a2c86" stroke-width="1.3" fill="none"/></svg>Bridges</li>
    <li><svg class="tick" viewBox="0 0 10 10"><circle cx="5" cy="5" r="5" fill="#2fc41e"/><path d="M2.8 5.2l1.5 1.5 2.9-3" stroke="#0a2c86" stroke-width="1.3" fill="none"/></svg>Clear Aligners</li>
  </ul>
  <ul class="service-column col-3">
    <li><svg class="tick" viewBox="0 0 10 10"><circle cx="5" cy="5" r="5" fill="#2fc41e"/><path d="M2.8 5.2l1.5 1.5 2.9-3" stroke="#0a2c86" stroke-width="1.3" fill="none"/></svg>Veneers</li>
    <li><svg class="tick" viewBox="0 0 10 10"><circle cx="5" cy="5" r="5" fill="#2fc41e"/><path d="M2.8 5.2l1.5 1.5 2.9-3" stroke="#0a2c86" stroke-width="1.3" fill="none"/></svg>Whitening</li>
    <li><svg class="tick" viewBox="0 0 10 10"><circle cx="5" cy="5" r="5" fill="#2fc41e"/><path d="M2.8 5.2l1.5 1.5 2.9-3" stroke="#0a2c86" stroke-width="1.3" fill="none"/></svg>Fillings</li>
  </ul>
  <ul class="service-column col-4">
    <li><svg class="tick" viewBox="0 0 10 10"><circle cx="5" cy="5" r="5" fill="#2fc41e"/><path d="M2.8 5.2l1.5 1.5 2.9-3" stroke="#0a2c86" stroke-width="1.3" fill="none"/></svg>Cleanings</li>
    <li><svg class="tick" viewBox="0 0 10 10"><circle cx="5" cy="5" r="5" fill="#2fc41e"/><path d="M2.8 5.2l1.5 1.5 2.9-3" stroke="#0a2c86" stroke-width="1.3" fill="none"/></svg>Dentures</li>
    <li><svg class="tick" viewBox="0 0 10 10"><circle cx="5" cy="5" r="5" fill="#2fc41e"/><path d="M2.8 5.2l1.5 1.5 2.9-3" stroke="#0a2c86" stroke-width="1.3" fill="none"/></svg>Overdentures</li>
  </ul>

  <div class="phone">
    <svg class="phone-icon" viewBox="0 0 42 42" aria-hidden="true">
      <circle cx="21" cy="21" r="21" fill="#ffffff"/>
      <path d="M14 11c1.5-1 3-.6 3.8.8l2 3.6c.6 1.1.3 2.3-.7 3l-1.5 1c1 2.6 2.9 4.6 5.3 5.8l1.1-1.4c.8-1 2.1-1.2 3.1-.5l3.4 2.2c1.3.9 1.6 2.4.6 3.8-1.6 2.2-4.1 3-6.6 2.1C17.6 29.3 12.6 24.1 10.9 17.5c-.6-2.6.8-5 3.1-6.5z" fill="#18b418"/>
      <path d="M23.5 12.5a7 7 0 0 1 6 6M23.5 8.5a11 11 0 0 1 10 10" stroke="#18b418" stroke-width="2" fill="none" stroke-linecap="round"/>
    </svg>
    <span class="phone-number">(555) 847-1390</span>
  </div>

  <div class="brand">
    <span class="brand-dot"></span>
    <span class="brand-name">Harlow Brook<br>Dentistry</span>
  </div>
</section>
</body>
</html>
```